Financial Advisor Resource Firm needs business card design

Need business card design for company in Omaha NE called Meridale Circle. We provide resources to financial advisors....workshop programs, retirement analysis, and insurance planning. I would like to see designs that use grays, greens, black, and white colors. The final design should communicate 'collaboration' and be simple yet attractive to financial planning clients. I will attached our logo and another picture of a puzzle piece coming together. I would like the incorporate the puzzle picture somehow, maybe on the back somehow, with color or just the gray scale....OR, the picture be the front of the card with 'Meridale' definition on it (see upload) and then company logo, employee name, title, address on the back (see ppt uploaded). The following disclosure needs to be included somewhere- Advisory services offered through Stonebrook Assets, LLC.
Updates

I uploaded a svg and ai file of the logo

Target Market(s)

Financial planning clients and financial advisors....so pretty diverse age range of about 40-70.

Industry/Entity Type

Financial Planning

Contact Information for Business Card

Tobias L. Fenwright, MBA
Founder/President
5287 E. Larkin Road
Suite 230
Omaha, NE 68190
Phone- (402) 555-0147
Cell- (402) 555-0183
Fax- (402) 555-0129
email- tobias@meridaleplan.example
web address- www.meridaleplan.example

Colors
1b1b1b
474747
d3d3d3
ffffff
9bcb3c
abd036

Requirements
Must have
• Must include logo provided, must be 2 sided, and must have disclosure...all of these items listed in project description

```html
<!DOCTYPE html>
<html lang="en">
<head>
<meta charset="utf-8">
<title>Meridale Circle – Business Card</title>
<link href="https://fonts.googleapis.com/css2?family=Lato:wght@400;700&display=swap" rel="stylesheet">
<style>
  :root {
    --backdrop: #2a2a2c;
    --card: #161616;
    --card-edge: #1f1f1f;
    --green: #8cc63f;
    --green-bright: #9bcb3c;
    --gray-light: #d3d3d3;
    --gray-mid: #9a9a9a;
    --gray-dark: #474747;
    --white: #ffffff;
  }
  * { box-sizing: border-box; margin: 0; padding: 0; }
  html, body {
    width: 1200px; height: 900px; overflow: hidden;
    background: var(--backdrop);
    font-family: "Lato", Arial, sans-serif;
  }
  .canvas { position: relative; width: 1200px; height: 900px; }

  .card {
    position: absolute; left: 320px; width: 560px; height: 320px;
    background: linear-gradient(160deg, var(--card-edge), var(--card));
    box-shadow: 0 14px 30px rgba(0,0,0,.45);
    overflow: hidden;
  }
  .card__band {
    position: absolute; left: 0; right: 0; bottom: 0; height: 11px;
    background: var(--green);
  }

  /* Front */
  .card--front { top: 90px; }
  .brand {
    position: absolute; left: 0; right: 0; top: 96px;
    display: flex; align-items: center; justify-content: center; gap: 14px;
  }
  .brand__dot {
    width: 22px; height: 22px; border-radius: 50%; background: var(--green-bright);
  }
  .brand__name {
    color: var(--white); font-weight: 700; font-size: 40px;
    letter-spacing: 2px; text-transform: uppercase;
  }
  .front__rule {
    position: absolute; left: 40px; right: 40px; top: 214px;
    height: 1px; background: var(--gray-dark);
  }
  .disclosure {
    position: absolute; left: 40px; right: 40px; top: 232px;
    color: var(--white); font-size: 14px; letter-spacing: .3px;
    text-transform: uppercase; text-align: center;
  }

  /* Back */
  .card--back { top: 470px; }
  .person {
    position: absolute; right: 300px; top: 78px; text-align: right;
  }
  .person__name {
    color: var(--green); font-weight: 700; font-size: 19px; text-transform: uppercase;
  }
  .person__name span { font-weight: 400; }
  .person__title { color: var(--gray-mid); font-size: 15px; margin-top: 2px; }
  .back__divider {
    position: absolute; left: 278px; top: 84px; width: 1px; height: 112px;
    background: var(--gray-dark);
  }
  .contacts {
    position: absolute; left: 292px; top: 84px; list-style: none;
  }
  .contacts li {
    display: flex; align-items: center; gap: 8px;
    color: var(--gray-light); font-size: 15px; line-height: 22px;
  }
  .contacts svg { width: 12px; height: 12px; fill: var(--green); flex: none; }
  .address {
    position: absolute; left: 0; right: 0; top: 236px; text-align: center;
    color: var(--white); font-size: 16px;
  }
</style>
</head>
<body>
<main class="canvas">

  <section class="card card--front">
    <div class="brand">
      <span class="brand__dot"></span>
      <span class="brand__name">Meridale Circle</span>
    </div>
    <div class="front__rule"></div>
    <p class="disclosure">Advisory services offered through Stonebrook Assets, LLC.</p>
    <div class="card__band"></div>
  </section>

  <section class="card card--back">
    <div class="person">
      <p class="person__name">Tobias L. Fenwright, <span>MBA</span></p>
      <p class="person__title">Founder/President</p>
    </div>
    <div class="back__divider"></div>
    <ul class="contacts">
      <li><svg viewBox="0 0 12 12"><path d="M1 4c0-2 1-3 3-3h4c2 0 3 1 3 3L9 5 8 3.5H4L3 5zM2 6h8l1 5H1z"/></svg>(402) 555-0147</li>
      <li><svg viewBox="0 0 12 12"><path d="M3 0h6v12H3zM4 1.5v8h4v-8z"/></svg>(402) 555-0183</li>
      <li><svg viewBox="0 0 12 12"><path d="M3 0h6v4H3zM0 4h12v6H10v2H2v-2H0zM3 8v3h6V8z"/></svg>(402) 555-0129</li>
      <li><svg viewBox="0 0 12 12"><path d="M0 2h12v8H0zM1 3l5 4 5-4v-.3H1z"/></svg>tobias@meridaleplan.example</li>
      <li><svg viewBox="0 0 12 12"><circle cx="6" cy="6" r="5.5"/></svg>www.meridaleplan.example</li>
    </ul>
    <p class="address">5287 E. Larkin Road Suite 230 Omaha, NE 68190</p>
    <div class="card__band"></div>
  </section>

</main>
</body>
</html>
```